Marava Cove Lodge Christmas wishes 2013

We require postcards designed to mail our to our clients for Christmas. We are a SURF travel company, with a high end market and like to mail our Christmas postcards to all our guests that have stayed with us through the year. Front cover will have images and text (ie Seasons Greeting) and our logo. The back will have space for TO: name & address and postage stamp. Will also have some basic text (ie The Management & Staff at Marava Cove Lodge wish you and your family all the best for the Festive Season and New Year. We look forward to seeing you back at Marava Cove Lodge again soon etc etc). Here is link to main image https://www.filecrate-example.com/sh/qwmxrtz481plo/Vb7kRtPwqN

Target Market(s)

Our clients are mostly mature men (40-70) surfers who purchase luxury surf trips

Industry/Entity Type

Travel

Requirements
Must have
• Ocean Image (front)
Logo x 2 in same colour - Orindel & Marava Cove Lodge (front)
Text (front)
Back to be white
Space for name & address (back)
Space for postage stamp (back)
Message (back)
Website www.orindellodges-example.com (back)

```html
<!DOCTYPE html>
<html lang="en">
<head>
<meta charset="utf-8">
<title>Marava Cove Lodge – Season's Greetings Postcard</title>
<link href="https://fonts.googleapis.com/css2?family=Dosis:wght@300;400;500&display=swap" rel="stylesheet">
<style>
  :root {
    --paper: #ffffff;
    --gold: #b07a35;
    --gold-soft: #d9a566;
    --gold-pale: #f6dc92;
    --cream: #fff6e0;
    --haze: #e0a348;
    --haze-light: #f2c470;
    --glare: #fff3c4;
    --sea: #d59440;
    --wet-sand: #e8ad55;
    --sand: #b87a2c;
    --sand-dark: #5e3810;
  }
  * { margin: 0; padding: 0; box-sizing: border-box; }
  html, body { width: 891px; height: 1200px; overflow: hidden; background: var(--paper); }
  .postcard {
    position: relative;
    width: 891px;
    height: 1200px;
    font-family: "Dosis", sans-serif;
    background: var(--paper);
    color: var(--gold);
  }
  .site-url {
    position: absolute;
    left: 33px;
    top: 20px;
    font-size: 18px;
    font-weight: 300;
    color: var(--gold-soft);
  }
  .stamp-box {
    position: absolute;
    left: 751px;
    top: 37px;
    width: 103px;
    height: 127px;
    border: 1.5px solid var(--gold);
  }
  .message {
    position: absolute;
    left: 253px;
    top: 78px;
    width: 380px;
    height: 150px;
  }
  .quote-mark {
    position: absolute;
    font-size: 100px;
    font-weight: 500;
    line-height: 1;
    color: var(--gold);
  }
  .quote-open { left: 0; top: -6px; }
  .quote-close { right: 6px; top: 110px; }
  .message-text {
    position: absolute;
    left: 20px;
    right: 20px;
    top: 21px;
    text-align: center;
    font-size: 20px;
    font-weight: 400;
    line-height: 25.5px;
  }
  .signature {
    position: absolute;
    left: 0;
    width: 891px;
    top: 274px;
    text-align: center;
    font-size: 14px;
    font-weight: 300;
    color: var(--gold-soft);
  }
  .address-lines {
    position: absolute;
    left: 277px;
    top: 394px;
    width: 361px;
  }
  .address-line {
    height: 36.5px;
    border-top: 1.5px solid var(--gold);
  }
  .photo-band {
    position: absolute;
    left: 0;
    top: 607px;
    width: 891px;
    height: 593px;
    background:
      radial-gradient(ellipse 170px 40px at 470px 195px, rgba(255,248,215,0.95), rgba(255,235,170,0) 100%),
      radial-gradient(ellipse 120px 20px at 400px 15px, rgba(255,245,210,0.8), rgba(255,235,170,0) 100%),
      radial-gradient(ellipse 300px 30px at 420px 210px, rgba(255,226,150,0.7), rgba(255,220,140,0) 100%),
      radial-gradient(ellipse 200px 230px at 150px 470px, rgba(255,205,110,0.75), rgba(240,180,80,0) 100%),
      radial-gradient(ellipse 420px 260px at 760px 560px, rgba(80,45,10,0.55), rgba(80,45,10,0) 100%),
      linear-gradient(180deg, var(--haze) 0%, var(--haze-light) 12%, var(--haze) 26%, #e6ab52 30%, var(--sea) 36%, #d18f3d 44%, var(--wet-sand) 52%, #c98b37 64%, var(--sand) 78%, #8d5a20 90%, var(--sand-dark) 100%);
  }
  .greeting {
    position: absolute;
    right: 82px;
    top: 657px;
    font-size: 58px;
    font-weight: 300;
    color: var(--cream);
    letter-spacing: 0.3px;
    text-shadow: 0 2px 4px rgba(120,70,10,0.35);
  }
  .greeting .accent { color: var(--gold-pale); }
  .brand-group {
    position: absolute;
    left: 28px;
    top: 1156px;
    display: flex;
    align-items: center;
    gap: 48px;
    font-size: 17px;
    font-weight: 400;
    letter-spacing: 3px;
    color: var(--cream);
    text-transform: uppercase;
  }
  .brand-dot {
    width: 34px;
    height: 34px;
    border-radius: 50%;
    background: var(--cream);
  }
  .lodge-mark {
    position: absolute;
    right: 38px;
    top: 1124px;
    text-align: center;
    color: var(--paper);
    font-weight: 400;
  }
  .lodge-name-row {
    display: flex;
    align-items: center;
    justify-content: center;
    gap: 8px;
    height: 34px;
  }
  .lodge-circle {
    width: 26px;
    height: 26px;
    border-radius: 50%;
    border: 2px solid var(--paper);
  }
  .lodge-name { font-size: 18px; }
  .lodge-url { display: block; font-size: 14px; line-height: 18px; margin-top: 2px; }
  .lodge-place { display: block; font-size: 11px; letter-spacing: 1px; line-height: 14px; }
</style>
</head>
<body>
  <main class="postcard">
    <p class="site-url">www.orindellodges-example.com</p>
    <div class="stamp-box" aria-label="Postage stamp space"></div>

    <section class="message">
      <span class="quote-mark quote-open">“</span>
      <p class="message-text">Wish you and your family all the best<br>for the Festive Season and New Year.<br>We look forward to seeing you back at<br>Marava Cove Lodge again soon...</p>
      <span class="quote-mark quote-close">”</span>
    </section>
    <p class="signature">The Management &amp; Staff at Marava Cove Lodge</p>

    <div class="address-lines" aria-label="Recipient name and address">
      <div class="address-line"></div>
      <div class="address-line"></div>
      <div class="address-line"></div>
      <div class="address-line"></div>
    </div>

    <div class="photo-band" role="img" aria-label="Golden sunset over a misty beach, surf breaking on the left, surfers and windsurf boards standing at the curving water's edge"></div>
    <h1 class="greeting">Season's <span class="accent">Greetings</span></h1>

    <div class="brand-group">
      <span class="brand-dot"></span>
      <span>Orindel Lodges &amp; Resorts</span>
    </div>

    <div class="lodge-mark">
      <div class="lodge-name-row">
        <span class="lodge-circle"></span>
        <span class="lodge-name">Marava Cove Lodge</span>
      </div>
      <span class="lodge-url">maravacovelodge-example.com</span>
      <span class="lodge-place">indonesia</span>
    </div>
  </main>
</body>
</html>
```